Business Card Design Project

Hi,
This is a simple contest. The logo for the back of the card is deigned. See attached files. The front of the card must have :

Directors Name: Tobias
Mob:
e-mail:
Postal Address:
Web Page Adress:

It may also add words: "Leaders in Construction Project Management Services"

Target Market(s)

Business & Home owners alike

Industry/Entity Type

Business

Requirements
Must have
• See details above and logo attached
Should not have
• Images other than logo

```html
<!DOCTYPE html>
<html lang="en">
<head>
<meta charset="utf-8">
<title>Kestrel Projects Australia – Business Card</title>
<link href="https://fonts.googleapis.com/css2?family=Open+Sans:wght@400;700&family=Questrial&display=swap" rel="stylesheet">
<style>
  :root {
    --page-bg: #ece9e4;
    --card-dark: #363636;
    --card-light: #ffffff;
    --brand-blue: #1b9ad6;
    --text-white: #ffffff;
    --text-grey: #7a7a7a;
    --divider: #d4d4d4;
  }
  * { margin: 0; padding: 0; box-sizing: border-box; }
  html, body { width: 1200px; height: 1000px; overflow: hidden; }
  body { background: var(--page-bg); position: relative; font-family: "Questrial", sans-serif; }

  .card { position: absolute; box-shadow: 0 4px 14px rgba(0,0,0,0.25); }

  /* Back of card */
  .card--back {
    left: 70px; top: 42px; width: 565px; height: 307px;
    background: var(--card-dark);
  }
  .brand {
    position: absolute; display: flex; align-items: center;
    font-family: "Open Sans", sans-serif; font-weight: 700;
  }
  .brand__square { flex: none; }
  .brand__rule { width: 2px; align-self: stretch; }
  .brand__words { display: flex; flex-direction: column; line-height: 1; }
  .brand__name { letter-spacing: 0.5px; }
  .brand__sub { letter-spacing: 3px; }

  .card--back .brand { left: 130px; top: 128px; gap: 10px; color: var(--text-white); }
  .card--back .brand__square { width: 54px; height: 54px; background: var(--text-white); }
  .card--back .brand__rule { background: var(--text-white); }
  .card--back .brand__name { font-size: 34px; }
  .card--back .brand__sub { font-size: 11px; margin-top: 4px; }
  .tagline {
    position: absolute; left: 130px; top: 192px; width: 305px;
    font-family: "Open Sans", sans-serif; font-size: 8.2px; letter-spacing: 0.4px;
    color: var(--text-white); text-align: center; white-space: nowrap;
  }

  /* Front of card */
  .card--front {
    left: 580px; top: 287px; width: 567px; height: 311px;
    background: var(--card-light); overflow: hidden;
  }
  .card--front .brand { left: 74px; top: 47px; gap: 12px; color: var(--brand-blue); }
  .card--front .brand__square { width: 72px; height: 72px; background: var(--brand-blue); }
  .card--front .brand__rule { background: var(--brand-blue); }
  .card--front .brand__name { font-size: 46px; }
  .card--front .brand__sub { font-size: 15px; margin-top: 4px; letter-spacing: 4px; }

  .person { position: absolute; right: 307px; top: 183px; text-align: right; color: var(--text-grey); }
  .person__name { font-size: 22px; color: var(--brand-blue); }
  .person__role { font-size: 7px; letter-spacing: 1.5px; color: var(--brand-blue); margin-left: 4px; }
  .person__address { font-size: 11.5px; line-height: 16px; margin-top: 12px; letter-spacing: 0.3px; }

  .split { position: absolute; left: 283px; top: 188px; width: 1px; height: 70px; background: var(--divider); }

  .contacts { position: absolute; left: 310px; top: 193px; list-style: none; font-size: 11.5px; color: var(--text-grey); letter-spacing: 0.3px; }
  .contacts li { display: flex; align-items: center; gap: 14px; height: 20.5px; }
  .contacts svg { width: 14px; height: 14px; fill: var(--brand-blue); flex: none; }

  .band-line { position: absolute; left: 0; right: 0; top: 289px; height: 1px; background: var(--divider); }
  .band { position: absolute; left: 0; top: 294px; width: 567px; height: 17px; }
  .band__label {
    position: absolute; right: 20px; top: 296px;
    font-family: "Open Sans", sans-serif; font-weight: 700; font-size: 11px;
    color: var(--text-white); letter-spacing: 0.3px;
  }
</style>
</head>
<body>

<section class="card card--back" aria-label="Card back">
  <div class="brand">
    <span class="brand__square"></span>
    <span class="brand__rule"></span>
    <span class="brand__words">
      <span class="brand__name">KESTREL</span>
      <span class="brand__sub">PROJECTS AUSTRALIA</span>
    </span>
  </div>
  <p class="tagline">LEADERS IN CONSTRUCTION PROJECT MANAGEMENT SERVICES</p>
</section>

<section class="card card--front" aria-label="Card front">
  <div class="brand">
    <span class="brand__square"></span>
    <span class="brand__rule"></span>
    <span class="brand__words">
      <span class="brand__name">KESTREL</span>
      <span class="brand__sub">PROJECTS AUSTRALIA</span>
    </span>
  </div>

  <div class="person">
    <p><span class="person__name">Tobias</span><span class="person__role">DIRECTOR</span></p>
    <p class="person__address">4410 Harbour Road Portside,<br>CA 90410</p>
  </div>

  <span class="split"></span>

  <ul class="contacts">
    <li>
      <svg viewBox="0 0 14 14"><rect x="4" y="1" width="6" height="12" rx="1"/><rect x="5" y="2.5" width="4" height="6" fill="#fff"/></svg>
      555 214 907
    </li>
    <li>
      <svg viewBox="0 0 14 14"><rect x="0.5" y="3" width="13" height="8.5"/><path d="M1 3.5 L7 8 L13 3.5" stroke="#fff" stroke-width="1.2" fill="none"/></svg>
      tobias@kestrelprojects.com
    </li>
    <li>
      <svg viewBox="0 0 14 14"><circle cx="7" cy="7" r="6" fill="none" stroke="var(--brand-blue)" stroke-width="1.2"/><ellipse cx="7" cy="7" rx="2.6" ry="6" fill="none" stroke="var(--brand-blue)" stroke-width="1"/><path d="M1 7 H13 M2 4 H12 M2 10 H12" stroke="var(--brand-blue)" stroke-width="1"/></svg>
      www.kestrelprojects.com
    </li>
  </ul>

  <span class="band-line"></span>
  <svg class="band" viewBox="0 0 567 17" aria-hidden="true">
    <polygon points="0,0 430,0 418,17 0,17" fill="var(--brand-blue)"/>
    <polygon points="440,0 567,0 567,17 428,17" fill="var(--brand-blue)"/>
    <polygon points="430,0 440,0 428,17 418,17" fill="#fff"/>
  </svg>
  <span class="band__label">KESTREL</span>
</section>

</body>
</html>
```